Indy Film Production Company/Studio

We need a business card designed from an existing logo. We are a digital studio/production company that caters to creating genre entertainment, like Action, Horror, and martial arts. The card along with the logo will be used to Brand the company from letter heads to banners. The design will also be used for postcards and Brochures. It should be professional and masculine.
Updates

Thank you to all the designers who have participated. I'm narrowing down who it will be. Thank you again.

Target Market(s)

Investors, Networks, Producers, and actors

Industry/Entity Type

Film Production

Contact Information for Business Card

Teodoro Valbuena
Producer/Writer/Director
www.kestrelpicturehouse.example

Requirements
Must have
• Website address, Facebook icon and Twitter icon possibly in the back of the card.
Nice to have
• Logline of Company: Follow The Action.

```html
<!DOCTYPE html>
<html lang="en">
<head>
<meta charset="utf-8">
<title>Kestrel Picture House – Business Card</title>
<link rel="stylesheet" href="https://fonts.googleapis.com/css2?family=Exo+2:ital,wght@0,400;0,800;1,300;1,400&display=swap">
<style>
  :root {
    --page-bg: #d9d6d2;
    --card-bg: #eef0f1;
    --brand-red: #d41f26;
    --deep-red: #b3141b;
    --ink: #1e1e1e;
    --stripe-dark: #222222;
    --white: #ffffff;
  }
  * { margin: 0; padding: 0; box-sizing: border-box; }
  html, body {
    width: 1200px; height: 969px; overflow: hidden;
    background: var(--page-bg);
    font-family: "Exo 2", Arial, sans-serif;
  }
  .card {
    position: absolute; left: 100px; top: 200px;
    width: 1000px; height: 568px;
    background: var(--card-bg);
    border: 1px solid #c9cbcc;
    box-shadow: 0 10px 30px rgba(0,0,0,0.18);
    overflow: hidden;
  }
  .brand-name {
    position: absolute; left: 60px; top: 62px;
    color: var(--brand-red); font-weight: 800; text-transform: uppercase;
    line-height: 1;
  }
  .brand-name .primary { display: block; font-size: 118px; letter-spacing: 2px; }
  .brand-name .secondary { display: block; font-size: 44px; letter-spacing: 3px; margin-top: 8px; }
  .band { position: absolute; left: 0; top: 0; width: 1000px; height: 568px; }
  .person {
    position: absolute; left: 60px; top: 338px; color: var(--white);
  }
  .person-name { font-size: 33px; font-weight: 400; letter-spacing: 1px; text-transform: uppercase; line-height: 1.1; }
  .person-role { font-size: 25px; font-weight: 300; font-style: italic; letter-spacing: 1px; text-transform: uppercase; margin-top: 4px; }
  .social {
    position: absolute; left: 872px; top: 372px; display: flex; gap: 6px;
  }
  .social span { width: 30px; height: 30px; background: var(--deep-red); display: block; }
  .contact {
    position: absolute; right: 56px; top: 420px; list-style: none;
    font-size: 26px; font-style: italic; font-weight: 400; color: var(--ink);
  }
  .contact li { display: flex; align-items: center; justify-content: flex-end; gap: 14px; height: 41px; }
  .contact svg { width: 26px; height: 26px; flex: none; }
</style>
</head>
<body>
  <main class="card">
    <div class="brand-name" aria-label="Kestrel Picture House">
      <span class="primary">Kestrel</span>
      <span class="secondary">Picture House</span>
    </div>

    <svg class="band" viewBox="0 0 1000 568" aria-hidden="true">
      <polygon points="0,327 545,327 515,418 0,418" fill="var(--brand-red)"/>
      <polygon points="549,327 1000,327 1000,333 556,333 527,418 519,418" fill="var(--stripe-dark)"/>
    </svg>

    <div class="person">
      <p class="person-name">Teodoro Valbuena</p>
      <p class="person-role">Producer/Writer/Director</p>
    </div>

    <div class="social" aria-label="Social profiles">
      <span></span><span></span>
    </div>

    <ul class="contact">
      <li>555 0142 7788
        <svg viewBox="0 0 24 24" aria-label="phone"><path fill="var(--brand-red)" d="M6.6 10.8a15 15 0 0 0 6.6 6.6l2.2-2.2c.3-.3.7-.4 1-.2 1.1.4 2.3.6 3.6.6.6 0 1 .4 1 1V20c0 .6-.4 1-1 1A17 17 0 0 1 3 4c0-.6.4-1 1-1h3.5c.6 0 1 .4 1 1 0 1.3.2 2.5.6 3.6.1.3 0 .7-.2 1z"/></svg>
      </li>
      <li>teodoro@kestrelpicturehouse.example
        <svg viewBox="0 0 24 24" aria-label="email"><rect x="2" y="5" width="20" height="14" fill="var(--brand-red)"/><path d="M2 5l10 8 10-8" fill="none" stroke="var(--card-bg)" stroke-width="1.6"/></svg>
      </li>
      <li>www.kestrelpicturehouse.example
        <svg viewBox="0 0 24 24" aria-label="website"><circle cx="12" cy="12" r="10" fill="var(--brand-red)"/><path d="M2 12h20M12 2c3 3 3 17 0 20M12 2c-3 3-3 17 0 20" fill="none" stroke="var(--card-bg)" stroke-width="1.3"/></svg>
      </li>
    </ul>
  </main>
</body>
</html>
```